Hearthside Lending Relief

Please help us give our website a remake or a FACELIFT. It is not very good but it says what we need it to say. But the design is terrible.
I would like our new design font and logo to be used as the theme.

I also want more photos on the site.

I also want consistency with the pages so they look clean.

We want the professionals to do this, let's see what you got!

Thank you!
Updates

Project Deadline Extended
Reason: I can understand you want to be paid. So I will commit to the fee but I want you to have time to make a KICK ASS website for me dudes! Thanks

HI!  Just wanted to say thanks for your time on these.  A lot are great.  However the firefighters have nothing to do with Foreclosure.  We are saving peoples homes from the bank taking them and selling them.   I LOVE the house photos and the families on the website.  That is the direction we like.  THanks.

THANK U ALL FOR THE WORK!   I like a few ending in the numbers: 147  733  693  536  620  478  727  508     I will go over them and choose one soon.  Thank you.   You will be paid shortly. 

Requirements
Must have
• Bright, Upbeat photos. Color scheme should be in order. We like icons on the bottom. not just text.

```html
<!DOCTYPE html>
<html lang="en">
<head>
<meta charset="utf-8">
<title>Hearthside Lending Relief</title>
<link href="https://fonts.googleapis.com/css2?family=Open+Sans:wght@400;600;700&family=Gelasio:wght@400;700&display=swap" rel="stylesheet">
<style>
  :root {
    --maroon: #7a2a30;
    --maroon-dark: #5a1217;
    --maroon-light: #8f353b;
    --brand-red: #c4262e;
    --ink: #2a2a2a;
    --muted: #555;
    --phone: #5b6b3f;
    --news-green: #2c4a12;
    --rule: #d6d6d6;
    --footer-link: #d9a4a6;
    --white: #ffffff;
  }
  * { box-sizing: border-box; margin: 0; padding: 0; }
  html, body { width: 1200px; height: 1200px; overflow: hidden; background: var(--white); }
  body { position: relative; font-family: "Open Sans", Verdana, sans-serif; color: var(--ink); }

  .topbar { position: absolute; left: 0; top: 0; width: 1200px; height: 32px; background: var(--maroon); }
  .account-links { position: absolute; right: 222px; top: 7px; font-size: 12px; color: #f3dede; }
  .account-links span.sep { margin: 0 14px; }

  .brand { position: absolute; left: 209px; top: 76px; display: flex; align-items: center; gap: 12px; }
  .brand-mark { width: 58px; height: 58px; border-radius: 50%; background: var(--brand-red); }
  .brand-name { font-size: 22px; font-weight: 700; color: var(--ink); line-height: 1.1; width: 170px; }

  .hotline { position: absolute; right: 213px; top: 104px; font-size: 18px; font-weight: 600; color: var(--phone); }

  .main-nav { position: absolute; left: 204px; top: 167px; width: 789px; height: 54px;
    background: linear-gradient(#94393f, #6e2228); border-radius: 4px 4px 0 0; }
  .main-nav a { position: absolute; top: 17px; font-size: 15px; color: #f6e6e6; text-decoration: none; transform: translateX(-50%); white-space: nowrap; }
  .main-nav .divider { position: absolute; top: 6px; width: 1px; height: 42px; background: rgba(255,255,255,0.22); }

  .hero { position: absolute; left: 188px; top: 221px; width: 823px; height: 370px;
    background: linear-gradient(180deg, #eef4f7 0%, #d9c6a6 40%, #a98262 65%, #6e7f45 100%); }
  .slider-dots { position: absolute; left: 755px; bottom: 8px; display: flex; gap: 6px; }
  .slider-dots i { width: 13px; height: 13px; border-radius: 50%; background: #fff; display: block; }
  .slider-dots i.active { background: #b2454c; }

  .band { position: absolute; left: 188px; top: 591px; width: 823px; height: 215px;
    background: linear-gradient(#6f8050 0%, #b3bea0 45%, #ffffff 100%); }

  .portfolio { position: absolute; left: 217px; top: 609px; width: 764px; height: 197px;
    background: linear-gradient(#ededed, #e2e2e2); border-radius: 4px; box-shadow: 0 1px 4px rgba(0,0,0,0.15); }
  .portfolio-head { height: 42px; background: linear-gradient(#a9a9a9, #8d8d8d); border-radius: 4px 4px 0 0; }
  .portfolio-head h2 { font-weight: 400; font-size: 16px; color: #fff; padding: 10px 0 0 30px; }
  .portfolio .sep { position: absolute; top: 55px; width: 1px; height: 130px; background: #cfcfcf; }
  .project { position: absolute; top: 58px; width: 196px; }
  .project-photo { width: 196px; height: 65px; border: 1px solid #bbb; }
  .project p { font-size: 10.5px; line-height: 16px; color: #444; margin-top: 8px; }
  .read-more { display: block; text-align: right; font-size: 11px; font-weight: 600; color: var(--maroon-dark); text-decoration: none; margin-top: 2px; }

  .welcome { position: absolute; left: 224px; top: 833px; width: 503px; }
  .section-title { font-family: "Gelasio", Georgia, serif; font-size: 16px; color: var(--ink); padding-bottom: 6px; border-bottom: 1px solid var(--rule); }
  .section-title b { color: var(--maroon-dark); }
  .welcome p { font-size: 13.5px; line-height: 21.3px; color: var(--ink); margin-top: 8px; width: 485px; }

  .news { position: absolute; left: 760px; top: 831px; width: 215px; }
  .news-item { margin-top: 12px; }
  .news-item h3 { font-size: 13px; font-weight: 400; color: var(--news-green); }
  .news-item p { font-size: 10.5px; line-height: 17px; color: #444; margin-top: 2px; }
  .news-item a { font-size: 10.5px; font-weight: 600; color: var(--maroon-dark); text-decoration: underline; }

  .site-footer { position: absolute; left: 0; top: 1051px; width: 1200px; height: 149px;
    background: linear-gradient(#8a2a30, #6b1a20 55%, var(--maroon-dark)); }
  .social { position: absolute; left: 570px; top: 27px; display: flex; gap: 8px; }
  .social i { width: 27px; height: 27px; display: block; background: #d7d7d7; border-radius: 4px; }
  .social i.round { border-radius: 50%; }
  .footer-nav { position: absolute; left: 0; top: 75px; width: 1200px; text-align: center; font-size: 14px; font-weight: 700; color: var(--footer-link); }
  .footer-nav a { color: var(--footer-link); text-decoration: none; }
  .footer-nav .sep { margin: 0 22px; }
  .copyright { position: absolute; left: 0; top: 103px; width: 1200px; text-align: center; font-size: 10.5px; color: #f0d3d3; }
</style>
</head>
<body>
  <header class="topbar">
    <div class="account-links">Login<span class="sep">|</span>Register</div>
  </header>

  <div class="brand">
    <div class="brand-mark"></div>
    <div class="brand-name">Hearthside Lending Relief</div>
  </div>
  <div class="hotline">Call Toll Free Now : 877-555-0148</div>

  <nav class="main-nav">
    <a href="#" style="left:67px">Home</a>
    <span class="divider" style="left:141px"></span>
    <a href="#" style="left:204px">About Us</a>
    <span class="divider" style="left:279px"></span>
    <a href="#" style="left:347px">Services</a>
    <span class="divider" style="left:416px"></span>
    <a href="#" style="left:500px">Contact Us</a>
    <span class="divider" style="left:577px"></span>
    <a href="#" style="left:687px">Financing Options</a>
  </nav>

  <section class="hero" role="img" aria-label="Smiling family of four standing in front of a brick two-storey house">
    <div class="slider-dots"><i></i><i class="active"></i><i></i></div>
  </section>

  <div class="band"></div>

  <section class="portfolio">
    <div class="portfolio-head"><h2>Our Portfolio</h2></div>
    <div class="project" style="left:30px">
      <div class="project-photo" role="img" aria-label="Family posing in front of a brick wall" style="background:linear-gradient(90deg,#9a4a3a,#c99a7a,#7a5040)"></div>
      <p>This website is for a real estate development project in the Cayman Islands called Larchmere.</p>
      <a class="read-more" href="#">Read More</a>
    </div>
    <span class="sep" style="left:257px"></span>
    <div class="project" style="left:294px">
      <div class="project-photo" role="img" aria-label="Brick family house under a pale sky" style="background:linear-gradient(#e4e8ec,#b88a74 60%,#8a7a6a)"></div>
      <p>This website is for a real estate development project in the Cayman Islands called Larchmere.</p>
      <a class="read-more" href="#">Read More</a>
    </div>
    <span class="sep" style="left:520px"></span>
    <div class="project" style="left:540px">
      <div class="project-photo" role="img" aria-label="Single-storey home with autumn trees" style="background:linear-gradient(#6f9acb,#d27a3a 45%,#6e7a3a)"></div>
      <p>This website is for a real estate development project in the Cayman Islands called Larchmere.</p>
      <a class="read-more" href="#">Read More</a>
    </div>
  </section>

  <section class="welcome">
    <h2 class="section-title"><b>Welcome</b> to our site</h2>
    <p>This website is for a real estate development project in the Cayman Islands called Larchmere. The community, when complete, will largely target the North American retiree market and will feature a town centre complete with convenience and boutique style shopping, a sports centre that will host a championship Pro Links tour winner designed golf course, and single family and multi-family homes. A simple website is required for the introductory stages of this development to act as an information conduit for Cayman Islands.</p>
  </section>

  <aside class="news">
    <h2 class="section-title"><b>Latest</b> News</h2>
    <div class="news-item">
      <h3>Headlines goes here</h3>
      <p>dummy text of the printing and typesetting industry. Lorem Ipsum has.</p>
      <a href="#">Read More</a>
    </div>
    <div class="news-item">
      <h3>Headlines goes here</h3>
      <p>dummy text of the printing and typesetting industry. Lorem Ipsum.</p>
      <a href="#">Read More</a>
    </div>
  </aside>

  <footer class="site-footer">
    <div class="social"><i class="round"></i><i></i><i></i></div>
    <div class="footer-nav">
      <a href="#">Home</a><span class="sep">|</span><a href="#">About Us</a><span class="sep">|</span><a href="#">Services</a><span class="sep">|</span><a href="#">Contact Us</a><span class="sep">|</span><a href="#">Financing Options</a>
    </div>
    <div class="copyright">© COPYRIGHT 2012. ALL RIGHTS RESERVED.</div>
  </footer>
</body>
</html>
```